Wed site for biomedical device startup

We need a generic website for a medical device startup. I will provide examples below of websites from other companies that can serve as models for what we are looking for. The startup is for a device that can non invasively measure blood flow in the brain using light. The application is to detect the type of stroke someone is having before they get to the hospital so treatment can be started right away. This saves patients upto hours of delayed treatment. Patients will be able to recover from stroke much better and faster as a result. I have attached an AI generated illustration of what the device will ultimately look like for reference.

https://www.372clinicaltech.com
https://vextalune.com

Target Market(s)

Biomedical, medical device, investors of biomedical device startups

Industry/Entity Type

Biomedical

Coding

Coded - Design and coding required

Number of Pages Required

4 page

Requirements
Must have
• same section and section headings as example websites listed above
Nice to have
• similar to example websites listed above. Prefer a darker website over a lighter one. Perhaps dark blues to go with logo colors. A moving background image element at top of landing page could be cool. Something indicative of heartbeat, or neurons, or blood flow.

```html
<!DOCTYPE html>
<html lang="en">
<head>
<meta charset="utf-8">
<title>Lumavex — Precision Biomedical Science</title>
<link href="https://fonts.googleapis.com/css2?family=Lato:wght@400;700&display=swap" rel="stylesheet">
<style>
  :root{
    --navy:#03033d;
    --navy-deep:#020232;
    --hero-a:#1b2b8f;
    --hero-b:#0a0f5a;
    --purple:#8a4fd8;
    --white:#ffffff;
    --line:#3a3a78;
  }
  *{margin:0;padding:0;box-sizing:border-box}
  html,body{width:1200px;height:2921px;overflow:hidden}
  body{background:var(--navy);color:var(--white);font-family:'Lato',sans-serif;position:relative}
  .abs{position:absolute}
  h1,h2,h3{font-weight:700}
  .btn{position:absolute;display:flex;align-items:center;justify-content:center;width:159px;height:45px;font-size:19px;text-decoration:none}
  .btn-purple{background:var(--purple);color:var(--white)}
  .btn-light{background:var(--white);color:var(--navy)}
  .brand{display:flex;align-items:center;gap:14px;color:var(--white);font-weight:700;text-decoration:none}
  .brand-dot{border-radius:50%;background:linear-gradient(135deg,#2f6df0,#8a4fd8)}

  /* header */
  .site-header{left:0;top:0;width:1200px;height:102px;background:var(--navy)}
  .site-header .brand{position:absolute;left:124px;top:13px;font-size:44px;letter-spacing:4px}
  .site-header .brand-dot{width:64px;height:64px}
  .nav{position:absolute;left:492px;top:25px;display:flex;font-size:15.5px}
  .nav a{color:var(--white);text-decoration:none;height:35px;display:flex;align-items:center;padding:0 13px}
  .nav a.active{background:var(--purple)}
  .site-header .btn{left:930px;top:20px;font-size:20px}

  /* hero */
  .hero{left:0;top:102px;width:1200px;height:475px;background:radial-gradient(circle at 75% 40%,#2a3fb0 0%,var(--hero-a) 35%,var(--hero-b) 100%)}
  .hero h1{position:absolute;left:109px;top:60px;font-size:52px;line-height:67px}
  .hero p{position:absolute;left:110px;top:212px;width:500px;font-size:15.5px;line-height:28px}
  .hero .btn{left:110px;top:293px}
  .hero-figure{position:absolute;left:840px;top:20px;width:270px;height:450px;border-radius:120px 120px 30px 30px;background:linear-gradient(180deg,#d9602b 0%,#4a6fd0 25%,#6b8fe0 60%,#2d3f9a 100%);opacity:.75}

  /* who */
  .who{left:0;top:577px;width:1200px;height:611px}
  .who-bg{position:absolute;left:0;top:0;width:608px;height:611px;background:linear-gradient(135deg,#141c5e,#070840)}
  .who-photo{position:absolute;left:111px;top:95px;width:445px;height:430px;border-radius:14px;background:linear-gradient(135deg,#c8b9ad,#e9dfd6 50%,#8e9aa4)}
  .who h2{position:absolute;left:645px;top:75px;font-size:40px}
  .who .body{position:absolute;left:643px;top:132px;width:445px;font-size:15.5px;line-height:27.5px}
  .who .body p+p{margin-top:10px}
  .who .btn{left:643px;top:486px}

  /* technologies */
  .tech-intro{left:0;top:1270px;width:1200px;text-align:center}
  .tech-intro h2{font-size:40px}
  .tech-intro p{width:975px;margin:18px auto 0;font-size:15.5px;line-height:27.5px}
  .tech-row{left:0;width:1200px;height:291px}
  .tech-row .media{position:absolute;top:0;width:600px;height:291px}
  .tech-row h3{position:absolute;font-size:36px}
  .tech-row p{position:absolute;width:450px;font-size:15.5px;line-height:27.5px}
  .row-ai{top:1450px}
  .row-ai .media{left:600px;background:linear-gradient(90deg,#3b5dbd,#2438a8 45%,#5a7ad0)}
  .row-ai h3{left:111px;top:20px}
  .row-ai p{left:111px;top:78px}
  .row-ai .btn{left:112px;top:210px}
  .row-rx{top:1742px}
  .row-rx .media{left:0;background:linear-gradient(90deg,#6a86b8,#c9d6e6 50%,#8497b8)}
  .row-rx h3{left:641px;top:32px}
  .row-rx p{left:642px;top:88px}
  .row-rx .btn{left:643px;top:220px}

  /* contact */
  .contact{left:0;top:2118px;width:1200px;height:422px;background:radial-gradient(ellipse at 50% 50%,#1c2a86,#0c1262 70%,#0a0f55);text-align:center}
  .contact h2{position:absolute;left:0;width:1200px;top:100px;font-size:40px}
  .contact p{position:absolute;left:205px;width:790px;top:180px;font-size:15.5px;line-height:27.5px}
  .contact .btn{left:520px;top:270px}

  /* footer */
  .site-footer{left:0;top:2540px;width:1200px;height:381px}
  .footer-links{position:absolute;left:206px;top:110px}
  .footer-links h4,.footer-contact h4{font-size:20px;font-weight:700;margin-bottom:10px}
  .footer-links li{list-style:none;font-size:15.5px;line-height:28.5px;display:flex;align-items:center;gap:12px}
  .footer-links li::before{content:"";width:8px;height:8px;background:var(--white)}
  .site-footer .brand{position:absolute;left:445px;top:88px;font-size:52px;letter-spacing:5px}
  .site-footer .brand-dot{width:84px;height:84px}
  .socials{position:absolute;left:518px;top:216px;display:flex;gap:17px}
  .socials span{width:28px;height:28px;border-radius:50%;background:var(--white)}
  .socials span:first-child{background:var(--purple)}
  .footer-contact{position:absolute;left:881px;top:110px;font-size:15px}
  .footer-contact li{list-style:none;display:flex;gap:8px;line-height:27px;margin-bottom:12px}
  .footer-contact svg{flex:none;margin-top:2px}
  .footer-rule{position:absolute;left:111px;top:330px;width:979px;height:1px;background:var(--line)}
  .copyright{position:absolute;left:0;width:1200px;top:346px;text-align:center;font-size:15.5px}
</style>
</head>
<body>

<header class="site-header abs">
  <a class="brand" href="#"><span class="brand-dot"></span>Lumavex</a>
  <nav class="nav">
    <a class="active" href="#">Home</a><a href="#">About</a><a href="#">Technology</a><a href="#">Publications</a>
  </nav>
  <a class="btn btn-purple" href="#">Contact Us</a>
</header>

<section class="hero abs">
  <div class="hero-figure" role="img" aria-label="Glowing anatomical figure showing brain, spine and nervous system"></div>
  <h1>Revolutionizing Healthcare<br>Through Precision Science</h1>
  <p>Harnessing cutting-edge biomedical technology to unlock the future of personalized medicine.</p>
  <a class="btn btn-purple" href="#">Get Started</a>
</section>

<section class="who abs">
  <div class="who-bg" role="img" aria-label="Dark blue neural network background"></div>
  <div class="who-photo" role="img" aria-label="Patient wearing a forehead sensor band connected to a handheld monitor"></div>
  <h2>Who We Are</h2>
  <div class="body">
    <p>At Biomedical, we are driven by a single purpose: to transform lives through cutting-edge biomedical innovation. Founded by a team of scientists, engineers, and entrepreneurs, we bring together expertise in biotechnology, clinical research, and data science to create impactful solutions for real-world health challenges.</p>
    <p>With a focus on [e.g., early disease detection, precision diagnostics, regenerative medicine], our mission is to bridge the gap between discovery and patient care. We partner with academic institutions, healthcare providers, and industry leaders to accelerate the development and delivery of life-saving technologies.</p>
  </div>
  <a class="btn btn-light" href="#">Read More</a>
</section>

<section class="tech-intro abs">
  <h2>Our Technologies</h2>
  <p>At the forefront of biomedical innovation, we are developing next-generation technologies that are transforming healthcare from the ground up. Our platform integrates advanced engineering, biology, and AI to solve critical challenges in diagnostics, therapeutics, and patient monitoring.</p>
</section>

<section class="tech-row row-ai abs">
  <h3>AI-Driven Diagnostics</h3>
  <p>Harnessing the power of machine learning, our diagnostic tools analyze complex biomedical data to deliver rapid, accurate, and early detection of disease — enabling clinicians to make informed decisions faster than ever.</p>
  <a class="btn btn-light" href="#">Read More</a>
  <div class="media" role="img" aria-label="Clinicians reviewing a holographic body scan display"></div>
</section>

<section class="tech-row row-rx abs">
  <div class="media" role="img" aria-label="Lab researcher working at a microscope"></div>
  <h3>Precision Therapeutics</h3>
  <p>Our proprietary drug delivery systems target treatment at the cellular level, reducing side effects and improving patient outcomes. We focus on smart materials and biologics tailored to individual patient profiles.</p>
  <a class="btn btn-light" href="#">Read More</a>
</section>

<section class="contact abs" role="img" aria-label="Soft blue neuron network background">
  <h2>Contact Us</h2>
  <p>We’d love to hear from you. Whether you have a question about our technology, partnership opportunities, or just want to say hello — our team is ready to connect.</p>
  <a class="btn btn-light" href="#">Read More</a>
</section>

<footer class="site-footer abs">
  <div class="footer-links">
    <h4>Quick Links</h4>
    <ul><li>Home</li><li>About</li><li>Technology</li><li>Publications</li></ul>
  </div>
  <a class="brand" href="#"><span class="brand-dot"></span>Lumavex</a>
  <div class="socials" aria-label="Social links"><span></span><span></span><span></span><span></span></div>
  <div class="footer-contact">
    <h4>Contact Us</h4>
    <ul>
      <li><svg width="26" height="26" viewBox="0 0 26 26"><circle cx="13" cy="13" r="13" fill="#fff"/><path d="M9 7c1 0 2 3 1.5 3.5l-1 1c1 2 2.5 3.5 4.5 4.5l1-1c.5-.5 3.5.5 3.5 1.5 0 1.5-1.5 2.5-2.5 2.5C10 19 7 16 7 10c0-1 1-3 2-3z" fill="#03033d"/></svg>+1 (555) 010-2784</li>
      <li><svg width="26" height="26" viewBox="0 0 26 26"><circle cx="13" cy="13" r="13" fill="#fff"/><rect x="7" y="9" width="12" height="8" fill="none" stroke="#03033d" stroke-width="1.5"/><path d="M7 9l6 5 6-5" fill="none" stroke="#03033d" stroke-width="1.5"/></svg>hello@lumavex.example</li>
      <li><svg width="26" height="26" viewBox="0 0 26 26"><circle cx="13" cy="13" r="13" fill="#fff"/><path d="M13 6a5 5 0 0 1 5 5c0 4-5 9-5 9s-5-5-5-9a5 5 0 0 1 5-5z" fill="#03033d"/><circle cx="13" cy="11" r="2" fill="#fff"/></svg>48 Meridian Way<br>Halden, MA 02100<br>USA</li>
    </ul>
  </div>
  <div class="footer-rule"></div>
  <p class="copyright">Copyright © 2025. new Biomedical Startup.All Rights Reserved</p>
</footer>

</body>
</html>
```